Single-sided business card for restaurant velmora with new logo made on this site

Business card options with new logo including restaurant name, address, phone number and website. This business card is single-sided only and will be presented at the hostess desk for clients to take. I would like to see options based on a cream card background, a white card background, a yellow card background and a burgundy colored background. It needs to be elegant and traditional.

Target Market(s)

local and international crowd

Industry/Entity Type

restaurant

Contact Information for Business Card

address, website and phone number

Font styles to use
Serif

Colors
EE7325
F08F49
F5BC92
FAE3D3
FDF4ED

Requirements
Must have
• new logo, address, phone number, website
Should not have
• more than three colors

```html
<!DOCTYPE html>
<html lang="es">
<head>
<meta charset="utf-8">
<title>Velmora – Tarjeta de presentación</title>
<link rel="stylesheet" href="https://fonts.googleapis.com/css2?family=Marcellus&display=swap">
<style>
  :root {
    --page-bg: #e4e4e4;
    --card-bg: #ffffff;
    --frame-gold: #f4b331;
    --ink-brown: #3a1f1c;
    --wash-cream: #fdf3df;
  }
  * { margin: 0; padding: 0; box-sizing: border-box; }
  html, body {
    width: 1200px;
    height: 940px;
    overflow: hidden;
    background: var(--page-bg);
  }
  .canvas {
    position: relative;
    width: 1200px;
    height: 940px;
  }
  .business-card {
    position: absolute;
    left: 258px;
    top: 274px;
    width: 684px;
    height: 392px;
    background: var(--card-bg);
    border-radius: 24px;
    overflow: hidden;
    font-family: "Marcellus", Georgia, serif;
    font-weight: 400;
    color: var(--ink-brown);
  }
  .leaf-wash {
    position: absolute;
    left: 0;
    top: 20px;
    width: 390px;
    height: 372px;
  }
  .gold-frame {
    position: absolute;
    left: 19px;
    top: 17px;
    right: 18px;
    bottom: 17px;
    border: 4px solid var(--frame-gold);
  }
  .brand {
    position: absolute;
    left: 464px;
    top: 41px;
    width: 200px;
    text-align: center;
  }
  .brand-square {
    display: block;
    width: 84px;
    height: 84px;
    margin: 0 auto;
    background: var(--frame-gold);
  }
  .brand-name {
    display: block;
    margin-top: 14px;
    padding-left: 5px;
    font-size: 28px;
    letter-spacing: 5px;
    line-height: 1;
    color: var(--ink-brown);
  }
  .contact {
    position: absolute;
    left: 50px;
    top: 191px;
  }
  .address {
    font-style: normal;
    font-size: 15.5px;
    line-height: 19.2px;
    letter-spacing: 0.4px;
  }
  .reservations-label {
    margin-top: 11px;
    font-size: 15.5px;
    line-height: 19px;
    letter-spacing: 0.4px;
  }
  .phone {
    margin-top: 2px;
    font-size: 22px;
    line-height: 26px;
  }
  .website {
    margin-top: 8px;
    font-size: 15.5px;
    line-height: 19px;
    letter-spacing: 0.6px;
  }
</style>
</head>
<body>
<main class="canvas">
  <article class="business-card">
    <svg class="leaf-wash" role="img" aria-label="Faint cream background decoration of the brand symbol" viewBox="0 0 390 372">
      <defs>
        <radialGradient id="wash" cx="0.4" cy="0.75" r="0.7">
          <stop offset="0" stop-color="#fdf3df" stop-opacity="0.9"/>
          <stop offset="1" stop-color="#fdf3df" stop-opacity="0"/>
        </radialGradient>
      </defs>
      <rect width="390" height="372" fill="url(#wash)"/>
    </svg>

    <div class="gold-frame"></div>

    <div class="brand">
      <span class="brand-square"></span>
      <span class="brand-name">VELMORA</span>
    </div>

    <div class="contact">
      <address class="address">
        Restaurant Velmora<br>
        Jacaranda 417<br>
        Bahía Serena<br>
        Oaxaca CP 70412
      </address>
      <p class="reservations-label">Reservaciones</p>
      <p class="phone">958-555-0142</p>
      <p class="website">www.velmora.com.mx</p>
    </div>
  </article>
</main>
</body>
</html>
```